Flask Mint Studio needs wedding label designs!

Flask Mint Studio is looking for new wedding designs! Please look at http://www.flaskmintstudio.com/water-bottle-labels and http://www.flaskmintstudio.com/custom-water to get an idea of what we currently offer.

These new designs will be saved onto Flask Mint Studio so that customers can come and customize the text and/or add pictures on them for purchase as water bottle labels or custom label bottled water.

Designs must appeal to a broad audience so any and all styles will be considered. Some other sites to draw inspiration from are plumcards.com, velvora.com, altarinkqueens.com and fernly.com.

Questions? Ask away!

Target Market(s)

Target market is brides, mothers of brides and wedding planners.

Industry/Entity Type

Wedding

Requirements
Must have
• Designs must be at 300 dpi in CMYK. Width is 8.133" Height is 2.377" with a .125" bleed around all sides.

```html
<!DOCTYPE html>
<html lang="en">
<head>
<meta charset="utf-8">
<title>Wedding Water Bottle Labels – WBL01 &amp; WBL02</title>
<link rel="stylesheet" href="https://fonts.googleapis.com/css2?family=Fira+Sans+Condensed:ital,wght@1,500;1,600&family=Source+Sans+3:ital,wght@0,400;0,600;0,700;1,700&display=swap">
<style>
  :root {
    --stage-center: #ffffff;
    --stage-edge: #d4d4d4;
    --code-grey: #8a8a8a;
    --cocoa: #764b29;
    --cocoa-dark: #5e3714;
    --gold: #c1b25a;
    --teal: #1aaca0;
    --teal-text: #14a394;
    --fuchsia: #ec1f7f;
    --tangerine: #f6931f;
    --flame: #f15a24;
    --paper: #ffffff;
  }
  * { margin: 0; padding: 0; box-sizing: border-box; }
  html, body { width: 1200px; height: 900px; overflow: hidden; }
  body {
    position: relative;
    background: radial-gradient(ellipse at 50% 48%, var(--stage-center) 40%, var(--stage-edge) 100%);
    font-family: "Source Sans 3", sans-serif;
  }
  .design-code {
    position: absolute;
    left: 131px;
    font-family: "Source Sans 3", sans-serif;
    font-size: 21px;
    font-weight: 400;
    color: var(--code-grey);
    letter-spacing: 0.5px;
  }
  .design-code--one { top: 83px; }
  .design-code--two { top: 455px; }
  .bottle-label {
    position: absolute;
    left: 131px;
    width: 937px;
    height: 273px;
    filter: drop-shadow(2px 3px 3px rgba(0,0,0,0.28));
  }
  .bottle-label--hearts { top: 121px; }
  .bottle-label--swirls { top: 492px; }
  .names-hearts {
    font-family: "Fira Sans Condensed", sans-serif;
    font-style: italic;
    font-weight: 600;
    font-size: 38px;
    fill: var(--teal-text);
  }
  .date-hearts {
    font-family: "Fira Sans Condensed", sans-serif;
    font-style: italic;
    font-weight: 500;
    font-size: 21px;
    fill: var(--teal-text);
  }
  .names-swirls {
    font-family: "Source Sans 3", sans-serif;
    font-weight: 600;
    font-size: 34px;
    fill: var(--flame);
  }
  .date-swirls {
    font-family: "Source Sans 3", sans-serif;
    font-weight: 700;
    font-size: 21px;
    fill: var(--flame);
  }
  .thanks-swirls {
    font-family: "Source Sans 3", sans-serif;
    font-style: italic;
    font-weight: 700;
    font-size: 15px;
    fill: var(--flame);
  }
</style>
</head>
<body>

  <div class="design-code design-code--one">WBL01</div>
  <svg class="bottle-label bottle-label--hearts" viewBox="0 0 937 273" aria-label="Wedding label with hearts band">
    <rect class="cocoa-frame" x="0" y="0" width="937" height="273" fill="var(--cocoa)"/>
    <g role="img" aria-label="Band of scattered hearts in teal and gold">
      <rect x="0" y="57" width="937" height="159" fill="var(--gold)"/>
      <rect x="0" y="79" width="937" height="115" fill="var(--teal)"/>
    </g>
    <ellipse class="medallion-rim" cx="469" cy="136" rx="167" ry="87" fill="var(--cocoa)"/>
    <ellipse class="medallion-face" cx="469" cy="136" rx="154" ry="74" fill="var(--paper)"/>
    <text class="names-hearts" x="469" y="141" text-anchor="middle">Laura &amp; Vincent</text>
    <text class="date-hearts" x="469" y="169" text-anchor="middle">May 15, 2011</text>
  </svg>

  <div class="design-code design-code--two">WBL02</div>
  <svg class="bottle-label bottle-label--swirls" viewBox="0 0 937 273" aria-label="Wedding label with swirls band">
    <rect x="0" y="0" width="937" height="273" fill="var(--fuchsia)" role="img" aria-label="Pink background of light pink swirls"/>
    <rect class="cocoa-rule" x="0" y="57" width="937" height="159" fill="var(--cocoa-dark)"/>
    <rect x="0" y="78" width="937" height="117" fill="var(--tangerine)" role="img" aria-label="Orange band of darker orange swirls"/>
    <ellipse class="medallion-rim" cx="469" cy="131" rx="198" ry="95" fill="var(--cocoa-dark)"/>
    <ellipse class="medallion-face" cx="469" cy="131" rx="185" ry="82" fill="var(--paper)"/>
    <text class="names-swirls" x="469" y="120" text-anchor="middle">Laura &amp; Vincent</text>
    <text class="date-swirls" x="469" y="146" text-anchor="middle">May 15, 2011</text>
    <text class="thanks-swirls" x="469" y="179" text-anchor="middle">¡Thanks for sharing with us</text>
    <text class="thanks-swirls" x="469" y="197" text-anchor="middle">on this special day!</text>
  </svg>

</body>
</html>
```